Business Card for beauty technology startup

Design Glimora Business Card for a Beauty, based on the website identity and colors (https://www.glimora-example.com).
Glimora is a beauty tech startup that gathers helpful product info for beauty lovers and consumers (such as availability on stores, price range and product reviews) for makeup products. The card design must be young, colorful but clean, and very modern.

Target Market(s)

woman, 15-35

Industry/Entity Type

Cosmetics

Contact Information for Business Card

Full Name, address, phone

Font styles to use
Other font styles liked:
• Advent Pro

Colors
e34297
86cfc6
ffffff
5c5c5c
e8e8e8
e667a6
b2b2b2

Requirements
Must have
• One full colored side with a creative design and another with card info
• Use Color palette: #95C5C5 and/or #D38AA5
• Use fonts: Advent Pro
• Use website identity: https://www.glimora-example.com
Nice to have
• If needed extra font: Roboto

```html
<!DOCTYPE html>
<html lang="en">
<head>
<meta charset="utf-8">
<title>Glimora Business Card</title>
<link rel="stylesheet" href="https://fonts.googleapis.com/css2?family=Advent+Pro:wght@300;400&family=Roboto+Condensed:wght@400;700&family=Roboto:wght@400&display=swap">
<style>
  :root {
    --backdrop: #2b2b2b;
    --card-white: #f4f4f4;
    --brand-pink: #b98093;
    --text-gray: #555555;
    --stripe-gray: #b2b2b2;
    --divider-gray: #9a9a9a;
    --white: #ffffff;
  }
  * { margin: 0; padding: 0; box-sizing: border-box; }
  html, body { width: 1200px; height: 960px; overflow: hidden; background: var(--backdrop); }
  .canvas { position: relative; width: 1200px; height: 960px; }

  .card { position: absolute; width: 600px; height: 342px; border-radius: 22px; overflow: hidden; }

  .card-front { left: 314px; top: 113px; background: var(--card-white); }
  .brand-block { position: absolute; left: 60px; top: 74px; width: 232px; text-align: center; }
  .brand-dot { display: block; width: 92px; height: 92px; margin: 0 auto 26px; border: 3px solid var(--brand-pink); border-radius: 50%; }
  .brand-name-front { font-family: "Advent Pro", sans-serif; font-weight: 300; font-size: 40px; letter-spacing: 4px; color: var(--brand-pink); line-height: 1; }
  .divider { position: absolute; left: 303px; top: 58px; width: 2px; height: 206px;
    background: linear-gradient(to bottom, rgba(154,154,154,0), var(--divider-gray) 30%, var(--divider-gray) 70%, rgba(154,154,154,0)); }

  .contact { position: absolute; left: 340px; top: 66px; font-family: "Roboto", sans-serif; color: var(--text-gray); }
  .person-name { font-family: "Roboto Condensed", sans-serif; font-weight: 700; font-size: 20px; color: var(--brand-pink); line-height: 24px; }
  .person-role { font-family: "Roboto Condensed", sans-serif; font-size: 15px; line-height: 20px; margin-bottom: 16px; }
  .address { font-size: 14.5px; line-height: 19px; margin-bottom: 9px; }
  .contact-list { list-style: none; font-size: 14.5px; line-height: 19px; }
  .contact-list li { display: flex; align-items: center; gap: 9px; }
  .contact-list svg { width: 14px; height: 14px; fill: var(--brand-pink); flex: none; }

  .front-band { position: absolute; left: 0; bottom: 0; width: 600px; height: 42px; }
  .front-url { position: absolute; right: 40px; bottom: 13px; font-family: "Roboto", sans-serif; font-size: 13px; letter-spacing: 1.4px; color: var(--white); }

  .card-back { left: 311px; top: 472px; background: var(--brand-pink); }
  .brand-name-back { position: absolute; right: 44px; top: 246px; font-family: "Advent Pro", sans-serif; font-weight: 300; font-size: 50px; letter-spacing: 4px; color: var(--white); line-height: 1; }
  .back-url { position: absolute; right: 44px; top: 302px; font-family: "Roboto", sans-serif; font-size: 13px; letter-spacing: 2.2px; color: var(--white); }
</style>
</head>
<body>
<main class="canvas">
  <section class="card card-front">
    <div class="brand-block">
      <span class="brand-dot"></span>
      <div class="brand-name-front">GLIMORA</div>
    </div>
    <div class="divider"></div>
    <div class="contact">
      <div class="person-name">DANIEL REYES</div>
      <div class="person-role">CEO/FOUNDER</div>
      <div class="address">1420 Willowmere Lane<br>Larkfield, Alaska 34512</div>
      <ul class="contact-list">
        <li><svg viewBox="0 0 24 24"><path d="M6.6 10.8a15 15 0 0 0 6.6 6.6l2.2-2.2c.3-.3.7-.4 1-.2 1.1.4 2.3.6 3.6.6.6 0 1 .4 1 1V20c0 .6-.4 1-1 1A17 17 0 0 1 3 4c0-.6.4-1 1-1h3.5c.6 0 1 .4 1 1 0 1.3.2 2.5.6 3.6.1.3 0 .7-.2 1z"/></svg>555 014 2281</li>
        <li><svg viewBox="0 0 24 24"><path d="M7 1h10a2 2 0 0 1 2 2v18a2 2 0 0 1-2 2H7a2 2 0 0 1-2-2V3a2 2 0 0 1 2-2zm0 3v14h10V4z"/></svg>555 017 6630</li>
        <li><svg viewBox="0 0 24 24"><path d="M6 2h12v5H6zM3 8h18a2 2 0 0 1 2 2v7h-4v5H5v-5H1v-7a2 2 0 0 1 2-2zm4 8v4h10v-4z"/></svg>555 019 4472</li>
        <li><svg viewBox="0 0 24 24"><path d="M2 5h20v14H2zm2 2v1l8 5 8-5V7l-8 5z"/></svg>info@glimora-example.com</li>
      </ul>
    </div>
    <svg class="front-band" viewBox="0 0 600 42" aria-hidden="true">
      <polygon points="0,17 330,17 322,27 0,27" fill="var(--stripe-gray)"/>
      <polygon points="345,0 600,0 600,42 0,42 0,31 320,31" fill="var(--brand-pink)"/>
    </svg>
    <div class="front-url">www.glimora-example.com</div>
  </section>

  <section class="card card-back">
    <div class="brand-name-back">GLIMORA</div>
    <div class="back-url">www.glimora-example.com</div>
  </section>
</main>
</body>
</html>
```